A website where experts collaborate on your project

I am building a new website where experts (yes, like designers) collaborate on projects with the project owner. More minds = more collaboration = better end product. Please see Pelmora(dot)com for a quick landing page I created for collaborating on presentations (although there will be many project types offered)

I am looking for a DESIGNER LONG TERM, but for now, just need initial mock ups to show the web programmers.

I have 21 Word documents loosely designed, what I would like to see here is a theme. Please DO NOT GO OFF WHAT YOU CURRENTLY SEE AT PELMORA. What is up now is only a quick landing page.

You can view a Word doc of the homepage here:
https://www.filevanta.com/s/qx83kdm2/home.docx?dl=0

WHAT AM I LOOKING FOR?
A clean, well designed theme.

Here is a link to the logo:
https://www.filevanta.com/s/mr47tpz9/logo%20-%20horizontal.tif?dl=0
-----------------------------------------
Here are a few sites I like the design of and what I like about them:
www.quenbrook.com-all around my favorite, beautiful graphics, clean layout, bold use of colors on a dark background
Ravelto.com- clean layout, The use of humans and bubble style elements.
Mintharbor.com :) clean, bold, unique pop art style but professional
plumevault.com - From the unique colors and artwork and the ability of that art to not interfere with the important elements of the site
sparkwidgets.com-clean, nice colors, well organized and separated sections.
www.dunmereco.com-love the font, use of colors and sectionalized style

All in all, I am not picky and open to so many styles. I would ultimately like the designer I pick to design all 21 pages.
Updates

Hello everyone,Moving forward, I would like you all to pay special attention to the section in my brief titled "Here are a few sites I like the design of and what I like about them". Please see below, I handpicked each one of these as sites I really like. Thank you.Here are a few sites I like the design of and what I like about them:Ravelto.com- clean layout, The use of humans and bubble style elements.Mintharbor.com :) clean, bold, unique pop art style but professionalwriteraccess.com - From the unique colors and artwork and the ability of that art to not interfere with the important elements of the sitegrowthgeeks.com-clean, nice colors, well organized and separated sections.www.dunmereco.com-love the font, use of colors and sectionalized stylewww.quenbrook.com-beautiful graphics, clean layout, bold use of colors----------------------------------------- Added Tuesday, November 24, 2015

I updated the homepage, you can see it here:https://www.dropbox.com/s/kwlkbsookq3cg2m/1new%20homepage.docx?dl=0I am modeling it after my favorite designed site: triplelift.comI love the dark colors with the orange glowing style boldness of the buttons. It's real clean too. Added Tuesday, November 24, 2015

Target Market(s)

small business owners, marketers, freelancer writers, graphic designers,

Industry/Entity Type

Building

Number of Pages Required

5+ page

Requirements
Must have
• I can't think of anything the project must have.
Nice to have
• WHAT AM I LOOKING FOR?
• A clean, well designed theme. I had a designer do a bit of work putting elements together, I found it to be very plain, but I like the Application Page (https://www.filevanta.com/s/jb19ckr3/Pelmora-Website.ai?dl=0)
• Here is a link to the logo:
• https://www.filevanta.com/s/mr47tpz9/logo%20-%20horizontal.tif?dl=0
• Here are a few sites I like the design of and what I like about them:
• Ravelto.com- clean layout, The use of humans and bubble style elements.
• Mintharbor.com :) clean, bold, unique pop art style but professional
• plumevault.com - From the unique colors and artwork and the ability of that art to not interfere with the important elements of the site
• sparkwidgets.com-clean, nice colors, well organized and separated sections.
• www.dunmereco.com-love the font, use of colors and sectionalized style
• www.quenbrook.com-beautiful graphics, clean layout, bold use of colors
• -----------------------------------------
Should not have
• out of the boxed, templated style website. I want this site to be memorable and not look like a thousand others

```html
<!DOCTYPE html>
<html lang="en">
<head>
<meta charset="utf-8">
<title>Pelmora – Crowd Projects</title>
<link href="https://fonts.googleapis.com/css2?family=Raleway:wght@400;500;600;700&family=PT+Sans:wght@400;700&display=swap" rel="stylesheet">
<style>
:root{
  --orange:#e07c12;
  --orange-dark:#c0640a;
  --teal:#17a3c8;
  --teal-dark:#0d8fb3;
  --ink:#2f3438;
  --text:#555b60;
  --muted:#8e959a;
  --line:#dfe3e6;
  --panel:#e9edf0;
  --footer:#15191b;
  --mark:#c3c8cc;
  --white:#ffffff;
}
*{box-sizing:border-box;margin:0;padding:0}
html,body{width:715px;height:1200px;overflow:hidden;background:var(--white)}
body{position:relative;font-family:"PT Sans",Arial,sans-serif;color:var(--text)}
.abs{position:absolute}

/* header */
.site-header{position:absolute;left:0;top:0;width:715px;height:58px;background:var(--white);border-bottom:1px solid var(--line);z-index:3}
.brand{position:absolute;left:66px;top:20px;display:flex;align-items:center;gap:5px;font-family:"PT Sans",sans-serif;font-weight:700;font-size:15px;color:var(--orange)}
.brand-dot{width:14px;height:14px;border-radius:50%;background:var(--orange)}
.search{position:absolute;left:201px;top:16px;width:145px;height:28px;border:1px solid #d3d7da;border-radius:3px;display:flex;align-items:center;font-size:7px;color:var(--muted)}
.search .browse{padding:0 8px;border-right:1px solid #d3d7da;height:16px;line-height:16px;letter-spacing:.3px}
.search .kw{padding-left:9px;flex:1}
.search svg{margin-right:10px}
.dropdown{position:absolute;left:201px;top:46px;width:64px;height:44px;background:var(--white);border:1px solid #d3d7da;border-radius:2px;z-index:4;font-size:7px}
.dropdown div{height:21px;line-height:21px;padding-left:9px}
.dropdown .active{border-left:2px solid var(--teal);color:var(--ink);font-weight:700;border-bottom:1px solid var(--line)}
.nav{position:absolute;top:26px;left:405px;display:flex;gap:19px;font-family:"Raleway",sans-serif;font-size:7px;font-weight:500;color:var(--ink)}
.nav .current{color:var(--orange)}

/* hero */
.hero{position:absolute;left:0;top:58px;width:715px;height:322px;background:linear-gradient(90deg,#c9d8e4 0%,#a9c5dc 35%,#7fa7c8 60%,#4d5a66 80%,#3b434b 100%)}
.hero-title{position:absolute;left:91px;top:166px;font-family:"Raleway",sans-serif;font-weight:600;font-size:20px;color:#1f2428;letter-spacing:.2px}
.hero-sub{position:absolute;left:92px;top:195px;font-size:10.5px;color:#2f3438}
.btn-orange{position:absolute;left:92px;top:218px;width:86px;height:33px;background:linear-gradient(#e48518,var(--orange-dark));border-radius:2px;color:var(--white);font-family:"Raleway",sans-serif;font-size:8px;font-weight:500;text-align:center;line-height:33px;letter-spacing:.3px}
.hero-dots{position:absolute;left:343px;top:356px;display:flex;gap:5px}
.hero-dots span{width:7px;height:7px;border-radius:50%;border:1px solid #dfe7ee}

.section-title{font-family:"Raleway",sans-serif;font-weight:600;font-size:12px;color:var(--ink);letter-spacing:.2px}

/* filters */
.filters{position:absolute;left:66px;top:409px;width:134px}
.filter-row{height:26px;border-bottom:1px solid var(--line);display:flex;justify-content:space-between;align-items:center;font-family:"Raleway",sans-serif;font-size:7.5px;font-weight:500;color:#4a5055}
.price-block{border-bottom:1px solid var(--line);height:48px;position:relative}
.price-block .label{position:absolute;top:9px;left:0;font-family:"Raleway",sans-serif;font-size:7.5px;font-weight:500;color:#4a5055}
.slider{position:absolute;left:2px;top:27px;width:132px;height:3px;background:#dde1e4;border-radius:2px}
.slider .fill{position:absolute;left:18px;width:97px;height:3px;background:var(--teal)}
.slider .knob{position:absolute;top:-3px;width:8px;height:8px;border-radius:50%;background:var(--orange);border:1.5px solid #f3d3ac}
.price-block .min,.price-block .max{position:absolute;top:36px;font-size:6.5px;color:var(--muted)}
.btn-teal{position:absolute;left:66px;top:682px;width:84px;height:27px;background:linear-gradient(#1fb0d4,var(--teal-dark));border-radius:2px;color:var(--white);font-family:"Raleway",sans-serif;font-size:7px;font-weight:600;text-align:center;line-height:27px}

/* projects */
.projects-head{position:absolute;left:216px;top:409px;width:430px;height:24px;border-bottom:1px solid var(--line)}
.sort{position:absolute;right:0;top:-2px;display:flex;align-items:center;gap:5px;font-size:7px;color:var(--ink);letter-spacing:.3px}
.sort .select{width:40px;height:17px;border:1px solid #d3d7da;border-radius:2px;font-size:6.5px;color:var(--muted);padding-left:5px;line-height:15px;position:relative}
.sort .select::after{content:"";position:absolute;right:5px;top:7px;border:2.5px solid transparent;border-top-color:#777}
.project{position:absolute;left:216px;width:430px;height:75px;border:1px solid #d8dcdf;background:var(--white)}
.project.featured{background:linear-gradient(#1aa9cd,#0e93b7);border-color:#0e93b7}
.project-logo{position:absolute;left:11px;top:10px;width:78px;height:54px;border:1px solid #d8dcdf;background:var(--white);display:flex;align-items:center;justify-content:center}
.project-logo .mark{width:40px;height:18px;border-radius:2px;background:var(--mark)}
.project-body{position:absolute;left:97px;top:12px;width:252px}
.project-title{font-family:"Raleway",sans-serif;font-size:8px;font-weight:500;color:#3a3f43;margin-bottom:3px}
.project-text{font-size:7px;line-height:14px;color:var(--muted)}
.featured .project-title,.featured .project-text{color:var(--white)}
.price-tag{position:absolute;left:355px;top:10px;width:63px;height:54px;background:linear-gradient(#e48518,var(--orange-dark));color:var(--white);text-align:center}
.price-tag .amount{font-family:"Raleway",sans-serif;font-size:15px;font-weight:500;margin-top:6px;line-height:17px}
.price-tag .meta{font-size:6px;line-height:10px}

/* testimonials */
.testimonials{position:absolute;left:0;top:818px;width:715px;height:176px;background:var(--panel)}
.quote-card{position:absolute;top:64px;width:290px;height:64px}
.avatar{position:absolute;left:0;top:0;width:64px;height:64px;border-radius:50%;background:linear-gradient(#dfe6ec,#9aa6b0);border:2px solid var(--white)}
.quote{position:absolute;left:72px;top:9px;width:208px;font-size:6.5px;line-height:15px;color:var(--text)}
.quote-name{position:absolute;left:74px;top:42px;font-family:"Raleway",sans-serif;font-size:7.5px;font-weight:600;color:var(--orange)}
.t-dots{position:absolute;left:344px;top:149px;display:flex;gap:4px}
.t-dots span{width:6px;height:6px;border-radius:50%;background:#c9cfd3}
.t-dots .on{background:var(--teal)}

/* partners */
.partners{position:absolute;left:0;top:994px;width:715px;height:82px;display:flex;align-items:center;justify-content:space-between;padding:0 64px 0 70px}
.partner{height:16px;border-radius:2px;background:var(--mark)}

/* footer */
.site-footer{position:absolute;left:0;top:1076px;width:715px;height:124px;background:var(--footer);color:#c7ccd0}
.f-col{position:absolute;top:14px}
.f-rule{position:absolute;top:14px;width:1px;height:92px;background:#2a3034}
.f-small{font-size:6.8px;line-height:12px}
.f-title{font-family:"Raleway",sans-serif;font-size:11px;font-weight:500;color:var(--white);letter-spacing:.3px}
.socials{display:flex;gap:5px;margin-top:10px}
.socials span{width:12px;height:12px;border-radius:2px;background:#4c565c}
.links{display:grid;grid-template-columns:92px 80px;row-gap:7px;margin-top:9px;font-size:6.8px}
.contact{margin-top:9px;font-size:6.8px}
.contact div{display:flex;align-items:center;gap:4px;height:18.5px}
</style>
</head>
<body>

<header class="site-header">
  <div class="brand"><span>Pelmora</span><span class="brand-dot"></span></div>
  <div class="search">
    <span class="browse">BROWSE ▾</span>
    <span class="kw">Keywords</span>
    <svg width="7" height="7" viewBox="0 0 10 10"><circle cx="4" cy="4" r="3" fill="none" stroke="#999" stroke-width="1.4"/><line x1="6.3" y1="6.3" x2="9" y2="9" stroke="#999" stroke-width="1.4"/></svg>
  </div>
  <nav class="nav">
    <span class="current">HOME</span><span>PROJECTS</span><span>HOW IT WORKS?</span><span>PLANS</span><span>MY ACCOUNT</span>
  </nav>
</header>
<div class="dropdown"><div class="active">Freelancers</div><div>Projects</div></div>

<section class="hero" role="img" aria-label="Photo of a smiling businessman with colleagues in a bright office"></section>
<h1 class="hero-title">CONVERT MORE CUSTOMERS</h1>
<p class="hero-sub">Experience the power of experts collaborating on your project.</p>
<div class="btn-orange">GET STARTED</div>
<div class="hero-dots"><span></span><span></span><span></span></div>

<aside class="filters">
  <h2 class="section-title" style="margin-bottom:14px">FILTERS</h2>
  <div class="price-block">
    <span class="label">PRICE</span>
    <svg class="abs" style="right:0;top:11px" width="7" height="5" viewBox="0 0 8 5"><path d="M1 4 4 1 7 4" fill="none" stroke="#555" stroke-width="1.3"/></svg>
    <div class="slider"><div class="fill"></div><span class="knob" style="left:14px"></span><span class="knob" style="left:111px"></span></div>
    <span class="min" style="left:13px">$ 20</span><span class="max" style="right:4px">$ 1,000 +</span>
  </div>
  <div class="filter-row">COUNTRY<svg width="7" height="5" viewBox="0 0 8 5"><path d="M1 1 4 4 7 1" fill="none" stroke="#555" stroke-width="1.3"/></svg></div>
  <div class="filter-row">CATEGORIES<svg width="7" height="5" viewBox="0 0 8 5"><path d="M1 1 4 4 7 1" fill="none" stroke="#555" stroke-width="1.3"/></svg></div>
  <div class="filter-row">TIME LEFT<svg width="7" height="5" viewBox="0 0 8 5"><path d="M1 1 4 4 7 1" fill="none" stroke="#555" stroke-width="1.3"/></svg></div>
  <div class="filter-row">ACTIVE | EXPIRED<svg width="7" height="5" viewBox="0 0 8 5"><path d="M1 1 4 4 7 1" fill="none" stroke="#555" stroke-width="1.3"/></svg></div>
  <div class="filter-row">CONTAINS ADULT CONTENT<svg width="7" height="5" viewBox="0 0 8 5"><path d="M1 1 4 4 7 1" fill="none" stroke="#555" stroke-width="1.3"/></svg></div>
  <div class="filter-row">KEYWORDS<svg width="7" height="5" viewBox="0 0 8 5"><path d="M1 1 4 4 7 1" fill="none" stroke="#555" stroke-width="1.3"/></svg></div>
  <div class="filter-row">FOLLOWERS<svg width="7" height="5" viewBox="0 0 8 5"><path d="M1 1 4 4 7 1" fill="none" stroke="#555" stroke-width="1.3"/></svg></div>
</aside>
<div class="btn-teal">SAVE FILTER</div>

<div class="projects-head">
  <h2 class="section-title">CROWD PROJECTS</h2>
  <div class="sort">SORT : <span class="select">Price</span></div>
</div>

<article class="project" style="top:446px">
  <div class="project-logo" role="img" aria-label="Client logo placeholder"><span class="mark"></span></div>
  <div class="project-body">
    <h3 class="project-title">MORBI IN ANTE ARCU</h3>
    <p class="project-text">Lorem ipsum dolor sit amet, consectetur adipiscing elit. Sed justo ante, varius at semper nec, scelerisque sed erat. Etiam vel neque at ligula vulputate hendrerit et faucibus eros.</p>
  </div>
  <div class="price-tag"><div class="amount">$80</div><div class="meta">◷ 6 days left</div><div class="meta">● U.K</div></div>
</article>

<article class="project featured" style="top:538px">
  <div class="project-logo" role="img" aria-label="Client logo placeholder"><span class="mark"></span></div>
  <div class="project-body">
    <h3 class="project-title">DONEC UT TRISTIQUE EST</h3>
    <p class="project-text">Ut bibendum fermentum iaculis. Suspendisse convallis enim imperdiet, fermentum nulla eu, convallis nibh. Morbi at varius erat, ut viverra velit. Proin facilisis ipsum justo, eu sodales eros iaculis ut.</p>
  </div>
  <div class="price-tag"><div class="amount">$90</div><div class="meta">◷ 6 days left</div><div class="meta">● CA</div></div>
</article>

<article class="project" style="top:630px">
  <div class="project-logo" role="img" aria-label="Client logo placeholder"><span class="mark"></span></div>
  <div class="project-body">
    <h3 class="project-title">LOREM IPSUM DOLOR SIT AMET</h3>
    <p class="project-text">Vivamus mi turpis, tincidunt et metus vitae, tempus aliquet orci. Quisque euismod interdum suscipit. Nunc sed efficitur mi. Sed leo leo, tristique at arcu quis, eleifend imperdiet risus. Maecenas malesuada dapibus ipsum eget malesuada.</p>
  </div>
  <div class="price-tag"><div class="amount">$80</div><div class="meta">◷ 6 days left</div><div class="meta">● U.K</div></div>
</article>

<article class="project" style="top:722px">
  <div class="project-logo" role="img" aria-label="Client logo placeholder"><span class="mark"></span></div>
  <div class="project-body">
    <h3 class="project-title">PHASELLUS FAUCIBUS NULLA PRETIUM</h3>
    <p class="project-text">Lorem ipsum dolor sit amet, consectetur adipiscing elit. Sed justo ante, varius at semper nec, scelerisque sed erat. Etiam vel neque at ligula vulputate hendrerit et faucibus eros.</p>
  </div>
  <div class="price-tag"><div class="amount">$80</div><div class="meta">◷ 6 days left</div><div class="meta">● U.K</div></div>
</article>

<section class="testimonials">
  <h2 class="section-title abs" style="left:66px;top:26px">WHAT OUT CUSTOMERS SAY</h2>
  <div class="quote-card" style="left:66px">
    <div class="avatar" role="img" aria-label="Portrait photo of a customer"></div>
    <p class="quote">“ With Pelmora I have multiple experts perfecting my content and I only pay for the feedback I find valuable. It's perfect ”</p>
    <div class="quote-name">DALE MERRIN, CEO, HALVO 52</div>
  </div>
  <div class="quote-card" style="left:366px">
    <div class="avatar" role="img" aria-label="Portrait photo of a customer"></div>
    <p class="quote">“ Before you put any content in front of your audience, review it with Pelmora, you won't regret it ”</p>
    <div class="quote-name">OWEN TARREL, CEO, QUILLBY</div>
  </div>
  <div class="t-dots"><span></span><span class="on"></span><span></span></div>
</section>

<section class="partners" role="img" aria-label="Row of client logo placeholders">
  <span class="partner" style="width:62px"></span>
  <span class="partner" style="width:52px"></span>
  <span class="partner" style="width:48px"></span>
  <span class="partner" style="width:66px"></span>
  <span class="partner" style="width:42px"></span>
  <span class="partner" style="width:72px"></span>
  <span class="partner" style="width:46px"></span>
</section>

<footer class="site-footer">
  <div class="f-col f-small" style="left:66px;top:40px">
    <div style="color:var(--white)">Privacy Policy &nbsp;|&nbsp; Sitemap</div>
    <div style="margin-top:3px">Copyrights @ 2015 Pelmora.<br>All Right Reserved.</div>
    <div class="socials"><span></span><span></span><span></span><span></span><span></span></div>
  </div>
  <div class="f-rule" style="left:214px"></div>
  <div class="f-col" style="left:254px">
    <div class="f-title">QUICK LINKS</div>
    <div class="links"><span>Home</span><span>Privacy Policy</span><span>How It Works?</span><span>Sitemap</span><span>Plans?</span><span>Login</span><span>My Account</span></div>
  </div>
  <div class="f-rule" style="left:428px"></div>
  <div class="f-col" style="left:466px">
    <div class="f-title">GET IN TOUCH</div>
    <div class="contact">
      <div><svg width="6" height="8" viewBox="0 0 6 8"><path d="M3 0a3 3 0 0 1 3 3c0 2-3 5-3 5S0 5 0 3a3 3 0 0 1 3-3z" fill="var(--orange)"/></svg>123 Lorem Ipsm..., Lorem Ipsm - 123 456</div>
      <div><svg width="8" height="6" viewBox="0 0 8 6"><rect width="8" height="6" rx="1" fill="var(--orange)"/><path d="M0 .5 4 3.5 8 .5" fill="none" stroke="#15191b" stroke-width=".8"/></svg>info@pelmora.com</div>
      <div><svg width="8" height="7" viewBox="0 0 8 7"><rect width="8" height="7" rx="1.5" fill="var(--orange)"/></svg>+41 123 456 789 000</div>
      <div><svg width="8" height="7" viewBox="0 0 8 7"><rect width="8" height="7" rx="1" fill="var(--orange)"/><rect x="2" y="1.5" width="4" height="2" fill="#15191b"/></svg>+41 123 456 789 000</div>
    </div>
  </div>
</footer>

</body>
</html>
```